Sable Grove products by Voldrin. Beauty, skin care cosmetic products

We are an all natural and organic beauty product company looking for a logo an label design ideas. Our motto is to make products that are safe, natural, in harmony with the earth and that really work. Our products will contribute to the transition from the Old Earth to the Sable Grove (as the image of the two worlds suggests). The earths can be mixed in the label. The label example is a rough sketch.
Updates

The label needs to be 1 (one) inch high and 7 inch long.

Need extra days to review

Target Market(s)

Products made with natural and organic ingredients. Beauty and skin products

Requirements
Must have
• My project must be standing out. We want customers to be draw to he product on the shelf. Wow, this label is different? what is it? All natural? I must try it.
• Must be bold but not outrageous.
• The two earth can be placed on right and left side of the tree of life on the second attachment
Nice to have
• The two Earth can be in the back ground suggesting that this product takes us from chemically and artificially filled products to something new that is in harmony with nature and health.
Should not have
• Should not be boring. Ordinary, easy to forget and ignore patterns, lettering, logos.

```html
<!DOCTYPE html>
<html lang="en">
<head>
<meta charset="utf-8">
<title>Sable Grove Under-Arm-Balm Labels</title>
<link rel="stylesheet" href="https://fonts.googleapis.com/css2?family=Marcellus&family=Ubuntu:wght@400;700&display=swap">
<style>
  :root {
    --backdrop: #231f20;
    --label-blue: #1d52b8;
    --label-deep: #0b1a3d;
    --label-night: #070d20;
    --accent-green: #8cc63f;
    --ink-white: #ffffff;
    --ink-soft: #e6ecf7;
    --badge-red: #c8202f;
  }
  * { box-sizing: border-box; margin: 0; padding: 0; }
  html, body { width: 1200px; height: 972px; overflow: hidden; background: var(--backdrop); }
  .sheet { position: relative; width: 1200px; height: 972px; }
  .label {
    position: absolute; left: 92px; width: 1015px; height: 145px; overflow: hidden;
    background: linear-gradient(90deg, var(--label-blue) 0%, #1a3f8c 22%, var(--label-deep) 42%, var(--label-night) 50%, var(--label-deep) 58%, #1a3f8c 75%, var(--label-blue) 100%);
    color: var(--ink-white); font-family: "Marcellus", serif;
  }
  .earth-art { position: absolute; top: 0; height: 145px; }
  .earth-art.old { left: 0; width: 360px; background: radial-gradient(ellipse at 85% 50%, rgba(40,70,60,.55), transparent 65%); }
  .earth-art.new { right: 0; width: 420px; background: radial-gradient(ellipse at 20% 55%, rgba(70,120,230,.55), transparent 70%); }
  .tree-medallion {
    position: absolute; left: 348px; top: -30px; width: 320px; height: 205px; border-radius: 50%;
    background: radial-gradient(circle, #0a1633 0%, #0f2318 55%, #0a1226 75%, transparent 77%);
  }
  .ingredients { position: absolute; left: 22px; top: 16px; width: 285px; font-size: 8.6px; line-height: 11px; }
  .ingredients p + p { margin-top: 5px; }
  .warning { position: absolute; left: 15px; top: 104px; width: 275px; height: 30px; border: 1px solid var(--ink-white); padding: 3px 6px; font-size: 8.6px; line-height: 11px; }
  .scent { position: absolute; left: 318px; top: 0; width: 22px; height: 145px; display: flex; align-items: center; justify-content: center; }
  .scent span { transform: rotate(-90deg); white-space: nowrap; color: var(--accent-green); font-size: 15.5px; }
  .brand-block { position: absolute; left: 358px; top: 14px; width: 300px; text-align: center; }
  .brand-name { font-size: 20px; line-height: 22px; }
  .brand-by { font-size: 13px; line-height: 20px; }
  .brand-by b { font-family: "Ubuntu", sans-serif; font-size: 18px; font-weight: 700; }
  .product-name { font-family: "Ubuntu", sans-serif; font-weight: 700; color: var(--accent-green); font-size: 21px; line-height: 26px; margin-top: 9px; letter-spacing: .3px; }
  .claim { font-family: "Ubuntu", sans-serif; font-size: 11px; line-height: 16px; margin-top: 6px; }
  .claim-free { font-family: "Ubuntu", sans-serif; font-size: 10.5px; line-height: 15px; color: var(--ink-soft); }
  .claim-free b { color: var(--ink-white); }
  .maker { position: absolute; left: 727px; top: 25px; font-size: 9.5px; line-height: 12px; color: var(--ink-soft); }
  .learn { position: absolute; left: 727px; top: 67px; font-size: 9.5px; color: var(--ink-soft); }
  .learn strong { font-weight: 400; font-size: 12.5px; color: var(--ink-white); }
  .best-by { position: absolute; left: 727px; top: 99px; width: 102px; height: 15px; background: var(--ink-white); color: #333; font-size: 9px; line-height: 15px; padding-left: 5px; }
  .net-weight { position: absolute; left: 727px; top: 122px; font-size: 9.5px; color: var(--ink-soft); }
  .origin-badge { position: absolute; left: 845px; top: 100px; width: 35px; height: 35px; border-radius: 50%; background: var(--ink-white); border: 3px solid var(--badge-red); }
  .icon-column { position: absolute; left: 902px; top: 8px; width: 28px; }
  .icon-column svg { display: block; margin: 0 auto 5px; }
  .social-row { display: flex; justify-content: space-between; margin-bottom: 4px; }
  .social-dot { width: 13px; height: 13px; border-radius: 50%; background: var(--ink-white); }
  .barcode-panel { position: absolute; left: 942px; top: 9.5px; width: 62px; height: 127px; background: var(--ink-white); }
</style>
</head>
<body>
<div class="sheet">

  <!-- Label template repeated per scent -->
  <section class="label" style="top:92px">
    <div class="earth-art old" role="img" aria-label="Old Earth globe fading into the label"></div>
    <div class="earth-art new" role="img" aria-label="New blue Earth globe in the background"></div>
    <div class="tree-medallion" role="img" aria-label="Tree of life knotwork medallion"></div>
    <div class="ingredients">
      <p>INGREDIENTS: Organic Coconut (Cocos Nucifera) Oil, Organic Bees Wax, West African Shea (Butyrospermum Parkii) Butter, Arrowroot (Manihot Esculenta) Powder, Magnesium Oil, Nahcolite (Natural Baking Soda)</p>
      <p>DIRECTIONS: Using the tip of your finger or a spatula apply a pea size of balm to each underarm. Stinging may occur after shave. Wait a few minutes and then apply.</p>
    </div>
    <div class="warning">WARNING: External use only. Discontinue use if irritation occurs. Do not apply to open cuts or wounds.</div>
    <div class="scent"><span>Original Scent</span></div>
    <div class="brand-block">
      <div class="brand-name">Sable Grove Products</div>
      <div class="brand-by">by <b>VOLDRIN</b></div>
      <div class="product-name">UNDER-ARM-BALM</div>
      <div class="claim">100% NATURAL INGREDIENTS</div>
      <div class="claim-free"><b>No</b> Aluminum, <b>No</b> Parabens, <b>No</b> Phthalates</div>
    </div>
    <div class="maker">Manufactured by Voldrin<br>Fernhollow MD 20000</div>
    <div class="learn">Learn more at: <strong>VOLDRIN.COM</strong></div>
    <div class="best-by">Best by</div>
    <div class="net-weight">Net Wt. 2oz (56 g)</div>
    <div class="origin-badge"></div>
    <div class="icon-column">
      <svg width="26" height="24" viewBox="0 0 26 24"><rect x="3" y="8" width="20" height="14" rx="2" fill="none" stroke="#fff" stroke-width="1.6"/><line x1="2" y1="5" x2="24" y2="1" stroke="#fff" stroke-width="1.6"/></svg>
      <svg width="24" height="24" viewBox="0 0 24 24"><polygon points="12,2 22,20 2,20" fill="none" stroke="#8cc63f" stroke-width="2"/></svg>
      <svg width="24" height="20" viewBox="0 0 24 20"><circle cx="12" cy="10" r="8" fill="none" stroke="#fff" stroke-width="1.6"/></svg>
      <div class="social-row"><span class="social-dot"></span><span class="social-dot"></span></div>
      <div class="social-row"><span class="social-dot"></span><span class="social-dot"></span></div>
    </div>
    <div class="barcode-panel"></div>
  </section>

  <section class="label" style="top:253px">
    <div class="earth-art old" role="img" aria-label="Old Earth globe fading into the label"></div>
    <div class="earth-art new" role="img" aria-label="New blue Earth globe in the background"></div>
    <div class="tree-medallion" role="img" aria-label="Tree of life knotwork medallion"></div>
    <div class="ingredients">
      <p>INGREDIENTS: Organic Coconut (Cocos Nucifera) Oil, Organic Bees Wax, West African Shea (Butyrospermum Parkii) Butter, Arrowroot (Manihot Esculenta) Powder, Magnesium Oil, Nahcolite (Natural Baking Soda), White Fir (Abies Concolor) Essential Oil.</p>
      <p>DIRECTIONS: Using the tip of your finger or a spatula apply a pea size of balm to each underarm. Stinging may occur after shave. Wait a few minutes and then apply.</p>
    </div>
    <div class="warning">WARNING: External use only. Discontinue use if irritation occurs. Do not apply to open cuts or wounds.</div>
    <div class="scent"><span>White Fir</span></div>
    <div class="brand-block">
      <div class="brand-name">Sable Grove Products</div>
      <div class="brand-by">by <b>VOLDRIN</b></div>
      <div class="product-name">UNDER-ARM-BALM</div>
      <div class="claim">100% NATURAL INGREDIENTS</div>
      <div class="claim-free"><b>No</b> Aluminum, <b>No</b> Parabens, <b>No</b> Phthalates</div>
    </div>
    <div class="maker">Manufactured by Voldrin<br>Fernhollow MD 20000</div>
    <div class="learn">Learn more at: <strong>VOLDRIN.COM</strong></div>
    <div class="best-by">Best by</div>
    <div class="net-weight">Net Wt. 2oz (56 g)</div>
    <div class="origin-badge"></div>
    <div class="icon-column">
      <svg width="26" height="24" viewBox="0 0 26 24"><rect x="3" y="8" width="20" height="14" rx="2" fill="none" stroke="#fff" stroke-width="1.6"/><line x1="2" y1="5" x2="24" y2="1" stroke="#fff" stroke-width="1.6"/></svg>
      <svg width="24" height="24" viewBox="0 0 24 24"><polygon points="12,2 22,20 2,20" fill="none" stroke="#8cc63f" stroke-width="2"/></svg>
      <svg width="24" height="20" viewBox="0 0 24 20"><circle cx="12" cy="10" r="8" fill="none" stroke="#fff" stroke-width="1.6"/></svg>
      <div class="social-row"><span class="social-dot"></span><span class="social-dot"></span></div>
      <div class="social-row"><span class="social-dot"></span><span class="social-dot"></span></div>
    </div>
    <div class="barcode-panel"></div>
  </section>

  <section class="label" style="top:413px">
    <div class="earth-art old" role="img" aria-label="Old Earth globe fading into the label"></div>
    <div class="earth-art new" role="img" aria-label="New blue Earth globe in the background"></div>
    <div class="tree-medallion" role="img" aria-label="Tree of life knotwork medallion"></div>
    <div class="ingredients">
      <p>INGREDIENTS: Organic Coconut (Cocos Nucifera) Oil, Organic Bees Wax, West African Shea (Butyrospermum Parkii) Butter, Arrowroot (Manihot Esculenta) Powder, Magnesium Oil, Nahcolite (Natural Baking Soda), Lemongrass (Cymbopogon Citratus) Essential Oil</p>
      <p>DIRECTIONS: Using the tip of your finger or a spatula apply a pea size of balm to each underarm. Stinging may occur after shave. Wait a few minutes and then apply.</p>
    </div>
    <div class="warning">WARNING: External use only. Discontinue use if irritation occurs. Do not apply to open cuts or wounds.</div>
    <div class="scent"><span>Lemongrass</span></div>
    <div class="brand-block">
      <div class="brand-name">Sable Grove Products</div>
      <div class="brand-by">by <b>VOLDRIN</b></div>
      <div class="product-name">UNDER-ARM-BALM</div>
      <div class="claim">100% NATURAL INGREDIENTS</div>
      <div class="claim-free"><b>No</b> Aluminum, <b>No</b> Parabens, <b>No</b> Phthalates</div>
    </div>
    <div class="maker">Manufactured by Voldrin<br>Fernhollow MD 20000</div>
    <div class="learn">Learn more at: <strong>VOLDRIN.COM</strong></div>
    <div class="best-by">Best by</div>
    <div class="net-weight">Net Wt. 2oz (56 g)</div>
    <div class="origin-badge"></div>
    <div class="icon-column">
      <svg width="26" height="24" viewBox="0 0 26 24"><rect x="3" y="8" width="20" height="14" rx="2" fill="none" stroke="#fff" stroke-width="1.6"/><line x1="2" y1="5" x2="24" y2="1" stroke="#fff" stroke-width="1.6"/></svg>
      <svg width="24" height="24" viewBox="0 0 24 24"><polygon points="12,2 22,20 2,20" fill="none" stroke="#8cc63f" stroke-width="2"/></svg>
      <svg width="24" height="20" viewBox="0 0 24 20"><circle cx="12" cy="10" r="8" fill="none" stroke="#fff" stroke-width="1.6"/></svg>
      <div class="social-row"><span class="social-dot"></span><span class="social-dot"></span></div>
      <div class="social-row"><span class="social-dot"></span><span class="social-dot"></span></div>
    </div>
    <div class="barcode-panel"></div>
  </section>

  <section class="label" style="top:574px">
    <div class="earth-art old" role="img" aria-label="Old Earth globe fading into the label"></div>
    <div class="earth-art new" role="img" aria-label="New blue Earth globe in the background"></div>
    <div class="tree-medallion" role="img" aria-label="Tree of life knotwork medallion"></div>
    <div class="ingredients">
      <p>INGREDIENTS: Organic Coconut (Cocos Nucifera) Oil, Organic Bees Wax, West African Shea (Butyrospermum Parkii) Butter, Arrowroot (Manihot Esculenta) Powder, Magnesium Oil, Nahcolite (Natural Baking Soda), Fressia (Fressia Corymbosa) Essential Oil</p>
      <p>DIRECTIONS: Using the tip of your finger or a spatula apply a pea size of balm to each underarm. Stinging may occur after shave. Wait a few minutes and then apply.</p>
    </div>
    <div class="warning">WARNING: External use only. Discontinue use if irritation occurs. Do not apply to open cuts or wounds.</div>
    <div class="scent"><span>Freesia</span></div>
    <div class="brand-block">
      <div class="brand-name">Sable Grove Products</div>
      <div class="brand-by">by <b>VOLDRIN</b></div>
      <div class="product-name">UNDER-ARM-BALM</div>
      <div class="claim">100% NATURAL INGREDIENTS</div>
      <div class="claim-free"><b>No</b> Aluminum, <b>No</b> Parabens, <b>No</b> Phthalates</div>
    </div>
    <div class="maker">Manufactured by Voldrin<br>Fernhollow MD 20000</div>
    <div class="learn">Learn more at: <strong>VOLDRIN.COM</strong></div>
    <div class="best-by">Best by</div>
    <div class="net-weight">Net Wt. 2oz (56 g)</div>
    <div class="origin-badge"></div>
    <div class="icon-column">
      <svg width="26" height="24" viewBox="0 0 26 24"><rect x="3" y="8" width="20" height="14" rx="2" fill="none" stroke="#fff" stroke-width="1.6"/><line x1="2" y1="5" x2="24" y2="1" stroke="#fff" stroke-width="1.6"/></svg>
      <svg width="24" height="24" viewBox="0 0 24 24"><polygon points="12,2 22,20 2,20" fill="none" stroke="#8cc63f" stroke-width="2"/></svg>
      <svg width="24" height="20" viewBox="0 0 24 20"><circle cx="12" cy="10" r="8" fill="none" stroke="#fff" stroke-width="1.6"/></svg>
      <div class="social-row"><span class="social-dot"></span><span class="social-dot"></span></div>
      <div class="social-row"><span class="social-dot"></span><span class="social-dot"></span></div>
    </div>
    <div class="barcode-panel"></div>
  </section>

  <section class="label" style="top:734px">
    <div class="earth-art old" role="img" aria-label="Old Earth globe fading into the label"></div>
    <div class="earth-art new" role="img" aria-label="New blue Earth globe in the background"></div>
    <div class="tree-medallion" role="img" aria-label="Tree of life knotwork medallion"></div>
    <div class="ingredients">
      <p>INGREDIENTS: Organic Coconut (Cocos Nucifera) Oil, Organic Bees Wax, West African Shea (Butyrospermum Parkii) Butter, Arrowroot (Manihot Esculenta) Powder, Magnesium Oil, Nahcolite (Natural Baking Soda), Lilac (Syringa Vulgaris) Essential Oil</p>
      <p>DIRECTIONS: Using the tip of your finger or a spatula apply a pea size of balm to each underarm. Stinging may occur after shave. Wait a few minutes and then apply.</p>
    </div>
    <div class="warning">WARNING: External use only. Discontinue use if irritation occurs. Do not apply to open cuts or wounds.</div>
    <div class="scent"><span>Lilac</span></div>
    <div class="brand-block">
      <div class="brand-name">Sable Grove Products</div>
      <div class="brand-by">by <b>VOLDRIN</b></div>
      <div class="product-name">UNDER-ARM-BALM</div>
      <div class="claim">100% NATURAL INGREDIENTS</div>
      <div class="claim-free"><b>No</b> Aluminum, <b>No</b> Parabens, <b>No</b> Phthalates</div>
    </div>
    <div class="maker">Manufactured by Voldrin<br>Fernhollow MD 20000</div>
    <div class="learn">Learn more at: <strong>VOLDRIN.COM</strong></div>
    <div class="best-by">Best by</div>
    <div class="net-weight">Net Wt. 2oz (56 g)</div>
    <div class="origin-badge"></div>
    <div class="icon-column">
      <svg width="26" height="24" viewBox="0 0 26 24"><rect x="3" y="8" width="20" height="14" rx="2" fill="none" stroke="#fff" stroke-width="1.6"/><line x1="2" y1="5" x2="24" y2="1" stroke="#fff" stroke-width="1.6"/></svg>
      <svg width="24" height="24" viewBox="0 0 24 24"><polygon points="12,2 22,20 2,20" fill="none" stroke="#8cc63f" stroke-width="2"/></svg>
      <svg width="24" height="20" viewBox="0 0 24 20"><circle cx="12" cy="10" r="8" fill="none" stroke="#fff" stroke-width="1.6"/></svg>
      <div class="social-row"><span class="social-dot"></span><span class="social-dot"></span></div>
      <div class="social-row"><span class="social-dot"></span><span class="social-dot"></span></div>
    </div>
    <div class="barcode-panel"></div>
  </section>

</div>
</body>
</html>
```